Need business card with a logo for a hearing aid sales and audiology business. We have two Hearing Instrument Specialists and one Audiologist on staff. Over 25 years in business. Locally owned and operated. Financing available. Most insurances accepted.

Summit Audio Wellness LLC
48730 W Larchmont, Suite 7
Cedar Hollow, MT 59921
406-617-2084
www.summitaudiowell.example

Manager
Tobias Kerrell HIS COHC
License #71829046

Target Market(s)

50yr old + people with a hearing loss.

Industry/Entity Type

Business

Contact Information for Business Card

48730 W Larchmont, Suite 7
Cedar Hollow, MT 59921
406-617-2084
www.summitaudiowell.example

Manager
Tobias Kerrell HIS COHC
NLVE #71829046

Font styles to use
Serif
Sans Serif

Requirements
Must have
• Business name, Tobias's name and title(s) and contact information, License #, web address

```html
<!DOCTYPE html>
<html lang="en">
<head>
<meta charset="utf-8">
<title>Summit Audio Wellness – Business Card</title>
<link href="https://fonts.googleapis.com/css2?family=Open+Sans:wght@400;600;700&display=swap" rel="stylesheet">
<style>
  :root {
    --backdrop: #e6e3df;
    --card-white: #ffffff;
    --brand-navy: #1b4c8f;
    --brand-blue: #1666b5;
    --band-navy: #1d4f95;
    --text-dark: #2a2a2a;
    --rule-grey: #c9c9c9;
  }
  * { margin: 0; padding: 0; box-sizing: border-box; }
  html, body {
    width: 1200px; height: 1000px; overflow: hidden;
    background: var(--backdrop);
    font-family: "Open Sans", Arial, sans-serif;
  }
  .card {
    position: absolute; left: 265px; width: 666px; height: 398px;
    box-shadow: 0 4px 12px rgba(0,0,0,0.18);
    overflow: hidden;
  }
  .card-front { top: 73px; background: var(--card-white); }
  .card-back { top: 532px; background: var(--brand-navy); }

  .brand-lockup {
    position: absolute; display: flex; align-items: center; gap: 12px;
    font-weight: 600; white-space: nowrap;
  }
  .card-front .brand-lockup { right: 32px; top: 60px; color: var(--brand-navy); font-size: 32px; }
  .card-back .brand-lockup { left: 0; right: 0; top: 170px; justify-content: center; color: var(--card-white); font-size: 40px; }
  .brand-dot { border-radius: 50%; background: currentColor; flex: none; }
  .card-front .brand-dot { width: 26px; height: 26px; }
  .card-back .brand-dot { width: 32px; height: 32px; }

  .holder { position: absolute; left: 33px; top: 194px; }
  .holder-name { font-size: 19px; font-weight: 700; color: var(--brand-navy); letter-spacing: 0.2px; }
  .holder-creds { font-size: 15px; font-weight: 400; color: var(--brand-blue); margin-left: 5px; }
  .holder-role { font-size: 15px; color: var(--text-dark); margin-top: 1px; }

  .divider { position: absolute; left: 33px; top: 248px; width: 452px; height: 1px; background: var(--rule-grey); }

  .license { position: absolute; left: 33px; top: 268px; font-size: 15px; color: var(--text-dark); }

  .contact { position: absolute; right: 32px; top: 236px; text-align: right; font-size: 15px; color: var(--text-dark); line-height: 24px; }
  .contact-line { display: flex; justify-content: flex-end; align-items: center; gap: 6px; }
  .contact-line svg { width: 16px; height: 16px; fill: var(--brand-blue); }
  .company-block { margin-top: 4px; line-height: 21px; }
  .company-name { font-weight: 700; }

  .bands { position: absolute; left: 0; bottom: 0; width: 666px; height: 40px; }
</style>
</head>
<body>

<section class="card card-front" aria-label="Business card front">
  <div class="brand-lockup"><span class="brand-dot"></span>Summit Audio Wellness</div>

  <div class="holder">
    <div><span class="holder-name">TOBIAS KERRELL</span><span class="holder-creds">HIS COHC</span></div>
    <div class="holder-role">Manager</div>
  </div>

  <div class="divider"></div>
  <div class="license">License #71829046</div>

  <div class="contact">
    <div class="contact-line">406-617-2084
      <svg viewBox="0 0 24 24" aria-hidden="true"><path d="M6.6 10.8a15.1 15.1 0 0 0 6.6 6.6l2.2-2.2c.3-.3.7-.4 1-.2 1.1.4 2.3.6 3.6.6.6 0 1 .4 1 1V20c0 .6-.4 1-1 1A17 17 0 0 1 3 4c0-.6.4-1 1-1h3.5c.6 0 1 .4 1 1 0 1.3.2 2.5.6 3.6.1.3 0 .7-.2 1z"/></svg>
    </div>
    <div class="contact-line">www.summitaudiowell.example
      <svg viewBox="0 0 24 24" aria-hidden="true"><path d="M12 2a10 10 0 1 0 0 20 10 10 0 0 0 0-20zm6.9 6h-3a15.6 15.6 0 0 0-1.4-3.6A8 8 0 0 1 18.9 8zM12 4c.8 1.2 1.5 2.5 1.9 4h-3.8c.4-1.5 1.1-2.8 1.9-4zM4.3 14a8.2 8.2 0 0 1 0-4h3.4a16.5 16.5 0 0 0 0 4zm.8 2h3a15.6 15.6 0 0 0 1.4 3.6A8 8 0 0 1 5.1 16zm3-8h-3a8 8 0 0 1 4.4-3.6C8.9 5.6 8.4 6.8 8.1 8zM12 20c-.8-1.2-1.5-2.5-1.9-4h3.8c-.4 1.5-1.1 2.8-1.9 4zm2.3-6H9.7a14.7 14.7 0 0 1 0-4h4.6a14.7 14.7 0 0 1 0 4zm.2 5.6c.6-1.1 1.1-2.3 1.4-3.6h3a8 8 0 0 1-4.4 3.6zm1.8-5.6a16.5 16.5 0 0 0 0-4h3.4a8.2 8.2 0 0 1 0 4z"/></svg>
    </div>
    <div class="company-block">
      <div class="company-name">Summit Audio Wellness</div>
      <div>48730 W Larchmont, Suite 7</div>
      <div>Cedar Hollow, MT 59921</div>
    </div>
  </div>

  <svg class="bands" viewBox="0 0 666 40" aria-hidden="true">
    <polygon points="0,22 325,22 312,40 0,40" fill="var(--band-navy)"/>
    <polygon points="365,10 666,10 666,40 332,40" fill="var(--brand-blue)"/>
  </svg>
</section>

<section class="card card-back" aria-label="Business card back">
  <div class="brand-lockup"><span class="brand-dot"></span>Summit Audio Wellness</div>
</section>

</body>
</html>
```